Corporate Business Card

Very professional, Modern, Not to busy, include phone address email, website
(541) 617-4930, 18761 52nd Avenue S, Alder Bay, OR 97047, martin@plumlinegroup.com, varkoworks.com

Target Market(s)

Manufacturing

Industry/Entity Type

Aero, machining, manufacturing, Off road racing

Contact Information for Business Card

Phone, address email, website

```html
<!DOCTYPE html>
<html lang="en">
<head>
<meta charset="utf-8">
<title>Varko Works – Business Card</title>
<link rel="stylesheet" href="https://fonts.googleapis.com/css2?family=Lato:wght@400;700&display=swap">
<style>
  :root {
    --backdrop: #e4e4e4;
    --card: #ffffff;
    --panel: #f0efed;
    --divider: #c9c9c9;
    --navy: #1d3577;
    --red: #d7262b;
    --ink: #3a3a3a;
    --ink-soft: #4a4a4a;
  }
  * { box-sizing: border-box; margin: 0; padding: 0; }
  html, body {
    width: 1200px; height: 801px; overflow: hidden;
    background: var(--backdrop);
    font-family: "Lato", Arial, sans-serif;
  }
  .card {
    position: absolute; left: 352px;
    width: 521px; height: 299px;
    background: var(--card);
    overflow: hidden;
  }
  .card--front { top: 45px; }
  .card--back { top: 423px; }

  .brand-panel {
    position: absolute; left: 0; top: 0;
    width: 197px; height: 100%;
    background: var(--panel);
    border-right: 1px solid var(--divider);
    display: flex; align-items: center; justify-content: center;
  }
  .wordmark {
    display: flex; align-items: center; gap: 7px;
    color: var(--navy); font-weight: 700; white-space: nowrap;
  }
  .wordmark__square { background: var(--red); display: block; }
  .wordmark--small { font-size: 21px; }
  .wordmark--small .wordmark__square { width: 10px; height: 10px; }
  .wordmark--large { font-size: 38px; gap: 12px; }
  .wordmark--large .wordmark__square { width: 18px; height: 18px; }

  .holder { position: absolute; left: 225px; top: 27px; }
  .holder__name { color: var(--red); font-size: 20px; font-weight: 700; line-height: 1.1; }
  .holder__title { color: var(--ink-soft); font-size: 13px; margin-top: 3px; }

  .contacts { position: absolute; left: 225px; top: 187px; list-style: none; }
  .contacts__item {
    display: flex; align-items: center; gap: 6px;
    color: var(--ink); font-size: 14px; font-weight: 700;
    height: 21px; white-space: nowrap;
  }
  .contacts__item--address { margin-top: 6px; }
  .contacts__icon { width: 13px; height: 13px; fill: var(--red); flex: none; }

  .card--back .wordmark { position: absolute; left: 50%; top: 50%; transform: translate(-50%, -50%); }
  .corner-mark {
    position: absolute; right: 0; bottom: 0;
    width: 23px; height: 23px;
  }
</style>
</head>
<body>
  <section class="card card--front">
    <div class="brand-panel">
      <div class="wordmark wordmark--small"><span class="wordmark__square"></span>Varko Works</div>
    </div>
    <div class="holder">
      <h1 class="holder__name">Dana Whitfield</h1>
      <p class="holder__title">founder &amp; CEO</p>
    </div>
    <ul class="contacts">
      <li class="contacts__item">
        <svg class="contacts__icon" viewBox="0 0 16 16" aria-hidden="true"><path d="M8 0a8 8 0 1 0 0 16A8 8 0 0 0 8 0zm5.9 7h-2.4a12 12 0 0 0-1-4.6A6 6 0 0 1 13.9 7zM8 2c.7.9 1.4 2.7 1.5 5h-3C6.6 4.7 7.3 2.9 8 2zM5.5 2.4A12 12 0 0 0 4.5 7H2.1a6 6 0 0 1 3.4-4.6zM2.1 9h2.4a12 12 0 0 0 1 4.6A6 6 0 0 1 2.1 9zM8 14c-.7-.9-1.4-2.7-1.5-5h3c-.1 2.3-.8 4.1-1.5 5zm2.5-.4a12 12 0 0 0 1-4.6h2.4a6 6 0 0 1-3.4 4.6z"/></svg>
        varkoworks.com
      </li>
      <li class="contacts__item">
        <svg class="contacts__icon" viewBox="0 0 16 16" aria-hidden="true"><path d="M3.6 1.2 5.8 3.4c.4.4.4 1 0 1.4L4.7 6a9.5 9.5 0 0 0 5.3 5.3l1.2-1.1c.4-.4 1-.4 1.4 0l2.2 2.2c.4.4.4 1 0 1.4l-1.3 1.3c-.8.8-2 1-3 .5A17 17 0 0 1 .5 5.5c-.5-1-.3-2.2.5-3L2.2 1.2c.4-.4 1-.4 1.4 0z"/></svg>
        (541) 617-4930, 18761
      </li>
      <li class="contacts__item">
        <svg class="contacts__icon" viewBox="0 0 16 16" aria-hidden="true"><path d="M1 3h14v10H1z"/><path d="M1.5 3.5 8 8.2l6.5-4.7" fill="none" stroke="#fff" stroke-width="1.4"/></svg>
        martin@plumlinegroup.com
      </li>
      <li class="contacts__item contacts__item--address">
        <svg class="contacts__icon" viewBox="0 0 16 16" aria-hidden="true"><path d="M8 0a5.5 5.5 0 0 0-5.5 5.5C2.5 10 8 16 8 16s5.5-6 5.5-10.5A5.5 5.5 0 0 0 8 0zm0 7.7a2.2 2.2 0 1 1 0-4.4 2.2 2.2 0 0 1 0 4.4z"/></svg>
        52nd Avenue S, Alder Bay, OR 97047
      </li>
    </ul>
  </section>

  <section class="card card--back">
    <div class="wordmark wordmark--large"><span class="wordmark__square"></span>Varko Works</div>
    <svg class="corner-mark" viewBox="0 0 23 23" aria-hidden="true"><polygon points="23,0 23,23 0,23" fill="var(--red)"/></svg>
  </section>
</body>
</html>
```